KLV Plant Services

We are a heavy diesel mechanical business with additional air con certificates, remapping engine rebuilt

Contact Information for Business Card

Company Name, Director Name, Managing Director, Contact details, email and website

Font styles to use
Serif
Script

```html
<!DOCTYPE html>
<html lang="en">
<head>
<meta charset="utf-8">
<title>KLV Plant Services – Business Card</title>
<link rel="stylesheet" href="https://fonts.googleapis.com/css2?family=Open+Sans:wght@400;600;700&display=swap">
<style>
  :root {
    --page-bg: #e9e4dd;
    --card-bg: #f3eee7;
    --card-edge: #ffffff;
    --ink-navy: #2b2a63;
    --ink-dark: #2e2c3a;
    --divider: #2b2a63;
  }
  * { box-sizing: border-box; margin: 0; padding: 0; }
  html, body {
    width: 1200px;
    height: 1047px;
    overflow: hidden;
    background: var(--page-bg);
    font-family: "Open Sans", Arial, sans-serif;
  }
  .card {
    position: absolute;
    left: 120px;
    top: 260px;
    width: 960px;
    height: 527px;
    background: var(--card-bg);
    border: 2px solid var(--card-edge);
    border-radius: 26px;
    box-shadow: 0 6px 24px rgba(60, 50, 40, 0.12);
  }
  .brand {
    position: absolute;
    left: 104px;
    top: 190px;
    width: 370px;
    display: flex;
    align-items: center;
    gap: 18px;
  }
  .brand-dot {
    flex: none;
    width: 34px;
    height: 34px;
    border-radius: 50%;
    background: var(--ink-navy);
  }
  .brand-name {
    color: var(--ink-navy);
    font-weight: 700;
    font-size: 44px;
    line-height: 1.08;
  }
  .divider {
    position: absolute;
    left: 516px;
    top: 128px;
    width: 2px;
    height: 260px;
    background: var(--divider);
  }
  .contact {
    position: absolute;
    left: 562px;
    top: 120px;
    color: var(--ink-dark);
  }
  .contact-name {
    color: var(--ink-navy);
    font-weight: 700;
    font-size: 35px;
    line-height: 1.1;
    letter-spacing: 0.3px;
  }
  .contact-role {
    color: var(--ink-navy);
    font-size: 23px;
    margin-top: 4px;
  }
  .contact-list {
    list-style: none;
    margin-top: 22px;
    font-size: 23px;
    line-height: 33px;
  }
  .contact-list li {
    display: flex;
    align-items: center;
    gap: 10px;
  }
  .contact-icon {
    width: 20px;
    height: 20px;
    fill: var(--ink-dark);
    flex: none;
  }
  .contact-address {
    margin-top: 14px;
    font-size: 23px;
    line-height: 33px;
  }
</style>
</head>
<body>
  <div class="card">
    <div class="brand">
      <span class="brand-dot"></span>
      <span class="brand-name">KLV Plant Services</span>
    </div>

    <div class="divider"></div>

    <div class="contact">
      <div class="contact-name">DANIEL CARTER</div>
      <div class="contact-role">Managing Director</div>
      <ul class="contact-list">
        <li>
          <svg class="contact-icon" viewBox="0 0 24 24" aria-hidden="true"><path d="M6.6 10.8a15.1 15.1 0 0 0 6.6 6.6l2.2-2.2c.3-.3.7-.4 1-.2 1.1.4 2.3.6 3.6.6.6 0 1 .4 1 1V20c0 .6-.4 1-1 1C10.6 21 3 13.4 3 4c0-.6.4-1 1-1h3.5c.6 0 1 .4 1 1 0 1.3.2 2.5.6 3.6.1.3 0 .7-.2 1z"/></svg>
          <span>123 456 789</span>
        </li>
        <li>
          <svg class="contact-icon" viewBox="0 0 24 24" aria-hidden="true"><path d="M3 5h18c.6 0 1 .4 1 1v12c0 .6-.4 1-1 1H3c-.6 0-1-.4-1-1V6c0-.6.4-1 1-1zm1 2.2V17h16V7.2l-8 5.3z M4.6 7 12 11.9 19.4 7z"/></svg>
          <span>info@yourgmail.com</span>
        </li>
        <li>
          <svg class="contact-icon" viewBox="0 0 24 24" aria-hidden="true"><path d="M12 2a10 10 0 1 0 0 20 10 10 0 0 0 0-20zm-1 17.9A8 8 0 0 1 4.1 10.9L9 15.8v1c0 1.1.9 2 2 2zm6.9-2.5c-.3-.8-1-1.4-1.9-1.4h-1v-3c0-.6-.4-1-1-1H8v-2h2c.6 0 1-.4 1-1V7h2c1.1 0 2-.9 2-2v-.4a8 8 0 0 1 2.9 12.8z"/></svg>
          <span>www.yourwebsite.com</span>
        </li>
      </ul>
      <p class="contact-address">Your address, City<br>State, Zip 1234</p>
    </div>
  </div>
</body>
</html>
```